Bright Harbor Counseling Letterhead for hip modern business

I would like some ombre use of the colors in the logo hip letterhead that incorporates logo colors and feel, needs to connect with young professionals and college students. i need to be able to write letters to schools to excuse absences as well. i like color blocks on one side preferably using colors from the attached logo design.

Target Market(s)

high income young people, young adults and college students

Industry/Entity Type

mental health

Font styles to use
Serif
Sans Serif

Colors
0054AA
0677BA
7BADD7
CADEEF
E8F1F8
0094D4
00A9DD
6FCCEA
C7EBF8
E9F6FB
00AB8E
00BBA5
67D7C9
C6EFE9
E9F9F6
59FF00
82FF00
B8FF75
E3FFCB
F4FFEA
A7469A
B969AE
D3A5CF
EDDBEB
F8F0F9
6B429C
8869AF
B7A5CE
E3DAEB
F3F0F8

Requirements
Must have
• a modern hip feel, somewhat color

```html
<!DOCTYPE html>
<html lang="en">
<head>
<meta charset="utf-8">
<title>Bright Harbor Counseling — Letterhead</title>
<link rel="stylesheet" href="https://fonts.googleapis.com/css2?family=Lato:wght@300;400&display=swap">
<style>
  :root {
    --backdrop: #2e2e2e;
    --paper: #ffffff;
    --ink: #3a3a3a;
    --purple: #843f98;
    --violet: #6b55a8;
    --blue: #2f74c0;
    --teal: #45c2b0;
  }
  html, body {
    margin: 0;
    width: 1200px;
    height: 1051px;
    overflow: hidden;
    background: var(--backdrop);
  }
  .letterhead {
    position: absolute;
    left: 260px;
    top: 45px;
    width: 680px;
    height: 960px;
    background: var(--paper);
    overflow: hidden;
    font-family: "Lato", sans-serif;
  }
  .brand {
    position: absolute;
    left: 56px;
    top: 58px;
    display: flex;
    align-items: center;
    gap: 12px;
  }
  .brand-dot {
    width: 24px;
    height: 24px;
    border-radius: 50%;
    background: var(--violet);
  }
  .brand-name {
    font-weight: 300;
    font-size: 22px;
    letter-spacing: 0.5px;
    color: var(--ink);
  }
  .footer-band {
    position: absolute;
    left: 0;
    top: 0;
    width: 680px;
    height: 960px;
  }
  .contact {
    position: absolute;
    right: 22px;
    bottom: 22px;
    display: flex;
    align-items: flex-end;
    gap: 16px;
    color: #fff;
    font-size: 11px;
    line-height: 17px;
  }
  .contact-address {
    font-style: normal;
    text-align: right;
  }
  .contact-list { list-style: none; margin: 0; padding: 0; }
  .contact-list li { display: flex; align-items: center; gap: 6px; }
  .contact-icon { width: 12px; height: 12px; flex: none; }
</style>
</head>
<body>
  <main class="letterhead">
    <div class="brand">
      <span class="brand-dot"></span>
      <span class="brand-name">Bright Harbor Counseling</span>
    </div>

    <svg class="footer-band" viewBox="0 0 680 960" aria-hidden="true">
      <defs>
        <linearGradient id="band-fill" x1="0" y1="1" x2="1" y2="0">
          <stop offset="0" stop-color="#843f98"/>
          <stop offset="0.55" stop-color="#6b55a8"/>
          <stop offset="1" stop-color="#2f74c0"/>
        </linearGradient>
      </defs>
      <path class="band" d="M0,962 C260,962 420,790 680,770 L680,962 Z" fill="url(#band-fill)"/>
      <path class="band-rule" d="M0,948 C260,948 420,774 680,756" fill="none" stroke="var(--teal)" stroke-width="2"/>
    </svg>

    <div class="contact">
      <address class="contact-address">
        Unit 8 Maple Row, Lakeview,<br>Zip 4810, Mainland
      </address>
      <ul class="contact-list">
        <li>
          <svg class="contact-icon" viewBox="0 0 12 12"><circle cx="6" cy="6" r="6" fill="#fff"/><path d="M4 3.2 L5 4.6 L4.5 5.3 Q5.3 6.8 6.7 7.5 L7.4 7 L8.8 8 L8.2 8.9 Q5.2 8.8 3.1 3.8 Z" fill="var(--violet)"/></svg>
          (00) 05550 213 470
        </li>
        <li>
          <svg class="contact-icon" viewBox="0 0 12 12"><circle cx="6" cy="6" r="6" fill="#fff"/><rect x="3.3" y="3" width="5.4" height="6" rx="0.6" fill="var(--violet)"/></svg>
          (00) 05550 213 471
        </li>
        <li>
          <svg class="contact-icon" viewBox="0 0 12 12"><circle cx="6" cy="6" r="6" fill="#fff"/><rect x="3" y="4" width="6" height="4.2" fill="var(--violet)"/><path d="M3 4 L6 6.4 L9 4" stroke="#fff" stroke-width="0.7" fill="none"/></svg>
          hello@brightharborcare.com
        </li>
        <li>
          <svg class="contact-icon" viewBox="0 0 12 12"><circle cx="6" cy="6" r="6" fill="#fff"/><circle cx="6" cy="6" r="3" fill="none" stroke="var(--blue)" stroke-width="0.8"/><path d="M3 6 H9 M6 3 V9" stroke="var(--blue)" stroke-width="0.6"/></svg>
          www.brightharborcare.com
        </li>
      </ul>
    </div>
  </main>
</body>
</html>
```